2 x Digitize Logo | 2 x Business Cards | 2 x Fridge Magnets

We require 6 deliverables:
1. Residential logo redrawn (same just high quality for large print format).
2. Corporate logo redrawn (minor changes to wording and high quality for large print format).
3. New business card design for Furniture Removals (residential)
4. New business card design for Corporate Relocations (business)
5. New Fridge magnet for Furniture removals (residential)
6. New fridge magnet for Corporate Relocations (business)
1. Residential Logo
a. We require the logo to be translated into a high quality digital image with no modifications.
(see attached resilogo.jpg)
2. Residential Logo
a. We require the logo to be edited (add the word corporate relocations) be translated into a high quality digital image.
(see attached corplogo.jpg)
3. Using the resilogo please make a new business card for our business.
a. Please see the web site https://www.larkbendcarters.com.au for colours and inspiration.
b. The residential business card needs the following information:
i. Business Name (using the residential logo).
ii. Free Call: 1800 LB Cart (the L, B and Cart much be the same colour as the logo).
iii. Website: www.LarkbendCarters.com.au
iv. Address: 4/17 Ormsdale Court, VIC 3264
v. Email: cart@LarkbendCarters.com.au
vi. backof Card:
Review our service
www.PennantOrbit.com.au
Services: Local, Country, Interstate | Furniture Removals | Piano, Billiard Tables & Antiques
4. Using the corplogo please make a new business card for our business.
b. The corporate business card needs the following information:
i. Business Name (using the corporate logo).
v. Email: corporate@LarkbendCarters.com.au
vi. Back of Card:
Review our service
www.PennantOrbit.com.au
Services: Corporate relocations | Office equipment moves | Packing Service | Packing Materials
5. Using the resilogo please make a new fridge magent for our business.
b. The residential fidge magnet needs the following information:
iv. Services: Local, Country, Interstate | Furniture Removals | Piano, Billiard Tables & Antiques
6. Using the corplogo please make a new fridge magent for our business.
b. The corporate fidge magnet needs the following information:
iv. Services: Local, Country, Interstate | Corporate relocations
Target Market(s)
Residential Furniture Removals and Corporate Office relocations
Industry/Entity Type
Business
Contact Information for Business Card
Please see full brief for six items required
Requirements
Must have
- Clean simple, easy to read
Nice to have
- fresh, stand out, eye catching
Should not have
- plain, standard, boring, general

```html
<!DOCTYPE html>
<html lang="en">
<head>
<meta charset="utf-8">
<title>Larkbend Carters – Corporate Business Card</title>
<link rel="stylesheet" href="https://fonts.googleapis.com/css2?family=Open+Sans:wght@400;600&display=swap">
<style>
  :root {
    --backdrop: #3a332f;
    --card: #121212;
    --ink: #f2f2f2;
    --brand-red: #d8261f;
    --brand-green: #0e8c45;
  }
  * { box-sizing: border-box; margin: 0; padding: 0; }
  html, body { width: 1200px; height: 900px; overflow: hidden; }
  body {
    background: var(--backdrop);
    font-family: "Open Sans", Arial, sans-serif;
    color: var(--ink);
    position: relative;
  }
  .card {
    position: absolute;
    top: 255px;
    width: 520px;
    height: 300px;
    background: var(--card);
    border-radius: 3px;
    box-shadow: 0 10px 28px rgba(0,0,0,.45);
  }
  .card--front { left: 50px; }
  .card--back { left: 630px; }

  .brand {
    position: absolute;
    right: 34px;
    top: 46px;
    text-align: right;
  }
  .brand__name {
    display: flex;
    align-items: center;
    justify-content: flex-end;
    gap: 10px;
    font-size: 25px;
    font-weight: 600;
    color: var(--brand-red);
    letter-spacing: .5px;
    text-transform: uppercase;
  }
  .brand__dot {
    width: 14px; height: 14px;
    border-radius: 50%;
    background: var(--brand-green);
  }
  .brand__tagline {
    margin-top: 4px;
    font-size: 15px;
    color: var(--brand-green);
    letter-spacing: 1px;
    text-transform: uppercase;
  }

  .contact {
    position: absolute;
    left: 34px;
    bottom: 30px;
    list-style: none;
    font-size: 19px;
    line-height: 1.5;
  }
  .contact li { display: flex; align-items: center; gap: 10px; }
  .contact li.contact__address { margin-top: 8px; }
  .contact svg { width: 15px; height: 15px; fill: var(--brand-red); flex: none; }
  .accent-green { color: var(--brand-green); }
  .accent-red { color: var(--brand-red); }

  .review {
    position: absolute;
    left: 36px;
    top: 46px;
    font-size: 13px;
    text-transform: uppercase;
    letter-spacing: .3px;
  }
  .review__url {
    display: block;
    margin-top: 6px;
    margin-left: 12px;
    text-transform: none;
  }

  .services {
    position: absolute;
    left: 36px;
    bottom: 62px;
    font-size: 14px;
  }
  .services__title {
    color: var(--brand-green);
    text-transform: uppercase;
    font-size: 14px;
    font-weight: 400;
    margin-bottom: 2px;
  }
  .services ul { list-style: none; padding-left: 14px; line-height: 1.35; }
  .services li { position: relative; padding-left: 14px; }
  .services li::before {
    content: "";
    position: absolute;
    left: 0; top: 7px;
    width: 7px; height: 7px;
    border-radius: 50%;
    background: var(--brand-red);
  }
</style>
</head>
<body>

<section class="card card--front" aria-label="Business card front">
  <div class="brand">
    <div class="brand__name"><span class="brand__dot"></span>Larkbend Carters</div>
    <div class="brand__tagline">Corporate Relocations</div>
  </div>

  <ul class="contact">
    <li>
      <svg viewBox="0 0 24 24" aria-hidden="true"><path d="M6.6 10.8a15.1 15.1 0 0 0 6.6 6.6l2.2-2.2a1 1 0 0 1 1-.25 11.4 11.4 0 0 0 3.6.57 1 1 0 0 1 1 1V20a1 1 0 0 1-1 1A17 17 0 0 1 3 4a1 1 0 0 1 1-1h3.5a1 1 0 0 1 1 1c0 1.25.2 2.45.57 3.57a1 1 0 0 1-.25 1z"/></svg>
      <span>1800 <span class="accent-green">LB</span> <span class="accent-red">Cart</span></span>
    </li>
    <li>
      <svg viewBox="0 0 24 24" aria-hidden="true"><path d="M2 5h20v14H2z M3 6l9 7 9-7" stroke="#121212" stroke-width="1.5"/></svg>
      <span>cart@LarkbendCarters.com.au</span>
    </li>
    <li>
      <svg viewBox="0 0 24 24" aria-hidden="true"><circle cx="12" cy="12" r="10"/><path d="M2 12h20M12 2c3 3 3 17 0 20M12 2c-3 3-3 17 0 20" stroke="#121212" stroke-width="1.5" fill="none"/></svg>
      <span>www.LarkbendCarters.com.au</span>
    </li>
    <li class="contact__address">
      <svg viewBox="0 0 24 24" aria-hidden="true"><path d="M12 2a7 7 0 0 0-7 7c0 5 7 13 7 13s7-8 7-13a7 7 0 0 0-7-7zm0 9.5A2.5 2.5 0 1 1 12 6.5a2.5 2.5 0 0 1 0 5z"/></svg>
      <span>4/17 Ormsdale Court, VIC 3264</span>
    </li>
  </ul>
</section>

<section class="card card--back" aria-label="Business card back">
  <p class="review">Review our service
    <span class="review__url">www.PennantOrbit.com.au</span>
  </p>

  <div class="brand">
    <div class="brand__name"><span class="brand__dot"></span>Larkbend Carters</div>
    <div class="brand__tagline">Corporate Relocations</div>
  </div>

  <div class="services">
    <h2 class="services__title">Services:</h2>
    <ul>
      <li>Corporate relocations</li>
      <li>Office equipment moves</li>
      <li>Packing Service</li>
      <li>Packing Materials</li>
    </ul>
  </div>
</section>

</body>
</html>
```